Company Creation Website Redesign

Firmora88 is an Australian company creation website that specialises in creating company and trust documents. Our website was created in 2014 and we would like a new fresh look. We would like to maintain the same colour scheme of light blue and white. We feel the current landing page is a bit busy and would like something cleaner and more minimalist.

We would like all toolbar options to be the same but redesigned with better font, more aesthetically pleasing etc.

The website is built on AngularJS framework with HTML/CSS markup.

Please have a look at the current landing page.
firmora88.com.au

Target Market(s)

Accountants, those want to create company

Industry/Entity Type

Commerce

Coding

Coded - Design and coding required

Number of Pages Required

5+ page

Font styles to use
Sans Serif

Colors
0054AA
0677BA
7BADD7
CADEEF
E8F1F8

Requirements
Must have
• Attractive symbols
Nice to have
• Simple colour scheme
Should not have
• Busy images

```html
<!DOCTYPE html>
<html lang="en">
<head>
<meta charset="utf-8">
<title>Firmora88 — Company Registration</title>
<link href="https://fonts.googleapis.com/css2?family=Lato:wght@400;700;900&family=Exo+2:wght@600;700&family=Bitter:wght@600&display=swap" rel="stylesheet">
<style>
:root{
  --blue-deep:#0054aa;
  --blue:#0677ba;
  --sky:#7badd7;
  --mist:#cadeef;
  --ice:#e8f1f8;
  --nav:#3a8edb;
  --navy:#173f86;
  --band:#1b4f9f;
  --footer:#1c56a7;
  --star:#f47b20;
  --ink:#1d1d1f;
  --white:#ffffff;
}
*{margin:0;padding:0;box-sizing:border-box}
html,body{width:1200px;height:3839px;overflow:hidden}
body{position:relative;font-family:'Lato',sans-serif;color:var(--ink);background:var(--white)}
.abs{position:absolute}
.round{border-radius:50%}

/* header */
.topbar{left:0;top:0;width:1200px;height:75px;background:var(--white)}
.brand{left:84px;top:12px;display:flex;flex-direction:column;align-items:center;gap:5px}
.brand-mark{width:22px;height:22px;border-radius:4px;background:var(--blue)}
.brand-name{font-size:14px;font-weight:700;color:var(--navy)}
.contact-item{display:flex;align-items:center;gap:12px;top:22px;font-size:17px;font-weight:700;color:var(--ink)}
.icon-dot{width:32px;height:32px;border-radius:50%;background:var(--blue-deep);display:flex;align-items:center;justify-content:center}
.login{left:966px;top:18px;width:122px;height:42px;border-radius:21px;background:var(--blue-deep);color:var(--white);font-weight:700;font-size:17px;display:flex;align-items:center;justify-content:center}
.navbar{left:0;top:75px;width:1200px;height:52px;background:var(--nav)}
.nav-link{top:91px;font-size:15px;color:var(--white)}
.search{left:872px;top:85px;width:197px;height:31px;border:1px solid rgba(255,255,255,.7);border-radius:16px;color:var(--white);font-size:12px;padding:8px 14px;display:flex;justify-content:space-between;align-items:center}

/* hero */
.hero{left:0;top:127px;width:1200px;height:547px;background:linear-gradient(90deg,#c4d9ee 0%,#c9dcef 45%,#b9cde2 100%)}
.hero-photo{left:536px;top:127px;width:664px;height:547px;background:linear-gradient(90deg,rgba(201,220,239,1) 0%,#8ea6c2 30%,#6f8aab 60%,#9fb4cb 100%)}
.hero-kicker{left:112px;top:238px;font-family:'Exo 2',sans-serif;font-weight:700;font-size:54px;color:#4f9de0}
.hero-title{left:100px;top:306px;display:flex;align-items:center;gap:12px;font-family:'Exo 2',sans-serif;font-weight:700;font-size:52px;color:var(--ink)}
.hero-title .sq{width:38px;height:38px;border-radius:8px;background:var(--blue)}
.hero-text{left:109px;top:398px;width:370px;font-size:16px;line-height:26px;color:#2b3440}
.btn{border-radius:22px;background:var(--blue-deep);color:var(--white);font-weight:700;display:flex;align-items:center;justify-content:center}
.hero-btn{left:112px;top:501px;width:143px;height:44px;font-size:16px}
.dots{display:flex;gap:6px}
.dots span{width:11px;height:11px;border-radius:50%;border:1.5px solid #333;background:transparent}
.dots span.on{background:#2f8de0;border-color:#2f8de0}

/* about */
.about-frame{left:128px;top:753px;width:453px;height:340px;border:2px solid var(--sky)}
.about-photo{left:112px;top:738px;width:454px;height:342px;background:linear-gradient(135deg,#3a3f4a,#7c8fa6 50%,#c6ccd3)}
.about-title{left:611px;top:772px;font-family:'Exo 2',sans-serif;font-weight:700;font-size:30px;color:var(--blue-deep)}
.about-sub{left:611px;top:829px;font-size:14.5px;color:#3d8fd6}
.about-text{left:611px;top:864px;width:477px;font-size:14.5px;line-height:26px;text-align:justify;color:#222}
.about-btn{left:624px;top:1018px;width:128px;height:39px;font-size:16px}

/* reviews band */
.band{left:0;top:1125px;width:1200px;height:465px;background:linear-gradient(90deg,#1a4c9c,#1d56aa 60%,#1a4c9c)}
.band-note{left:140px;top:1186px;width:920px;text-align:center;font-size:16px;line-height:25px;font-weight:700;color:var(--white)}
.stars{display:flex;gap:9px}
.leave{left:600px;top:1260px;font-size:15px;font-weight:900;color:var(--white)}
.avatar{width:150px;height:150px;border-radius:50%;border:2px dashed var(--white);display:flex;align-items:center;justify-content:center}
.avatar span{width:132px;height:132px;border-radius:50%;background:var(--ice);display:flex;align-items:center;justify-content:center;font-family:'Exo 2',sans-serif;font-weight:700;font-size:56px;color:var(--blue-deep)}
.rev-name{font-size:18px;font-weight:900;color:var(--white)}
.rev-text{font-size:15.5px;line-height:26px;color:var(--white)}

/* video */
.video{left:112px;top:1687px;width:976px;height:407px;background:linear-gradient(180deg,#e9e9e9,#ffffff 40%,#f4f4f4)}
.video-art{left:112px;top:1687px;width:487px;height:407px;background:linear-gradient(180deg,#e6e6e6,#f7f7f7 60%,#d8d8d8)}
.video-split{left:599px;top:1687px;width:2px;height:407px;background:#222}
.video-text{left:640px;top:1712px;width:450px;text-align:center;font-family:'Bitter',serif;font-weight:600;font-size:40px;line-height:60px;color:#111}
.play{left:572px;top:1830px;width:55px;height:55px;border-radius:50%;background:var(--blue-deep);border:3px solid var(--white);box-shadow:0 0 0 1px #bbb}

/* how it works */
.how{left:0;top:2173px;width:1200px;height:432px;background:var(--ice)}
.section-title{width:1200px;left:0;text-align:center;font-weight:900;font-size:28px;color:var(--navy)}
.step{top:2313px;width:246px;height:229px;border-radius:22px;background:#bcd5ec;display:flex;flex-direction:column;align-items:center}
.step svg{margin-top:36px}
.step p{margin-top:auto;margin-bottom:22px;text-align:center;font-size:19px;line-height:30px;font-weight:700;color:#1f2630}

/* testimonials */
.testi{left:112px;top:2704px;width:977px;height:361px;background:var(--white);box-shadow:0 2px 8px rgba(0,0,0,.18)}
.testi-photo{left:115px;top:2707px;width:512px;height:355px;background:linear-gradient(180deg,#4a4a4a,#7a6a60 45%,#1f1f22)}
.testi-date{left:685px;top:2804px;font-size:14px;color:var(--navy)}
.testi-quote{left:660px;top:2836px;width:374px;text-align:center;font-size:18px;line-height:27px;color:#333}
.testi-name{left:660px;top:2934px;width:374px;text-align:center;font-size:25px;color:var(--blue)}

/* sponsors */
.sponsor{top:3242px;width:213px;height:99px;border-radius:12px;background:#c3d9ee;display:flex;align-items:center;justify-content:center;gap:10px;font-weight:900;font-size:22px;color:#1a1a1a}
.sponsor i{display:block;width:30px;height:30px;border-radius:6px;background:#1a1a1a}
.arrow{top:3273px;width:38px;height:38px;border-radius:50%;background:var(--white);border:1px solid #ccc;display:flex;align-items:center;justify-content:center}

/* footer */
.footer{left:0;top:3391px;width:1200px;height:448px;background:var(--footer)}
.f-head{top:3458px;font-size:20px;font-weight:900;color:var(--white)}
.f-rule{top:3495px;width:30px;height:2px;background:var(--white)}
.f-list{top:3512px;font-size:15px;line-height:26px;color:var(--white)}
.f-small{font-size:14px;line-height:23px;color:var(--white)}
.f-label{font-size:13px;color:#dfe9f6}
.f-input{left:813px;top:3583px;width:274px;height:38px;border-radius:19px;background:var(--white);font-size:12px;color:#333;padding:0 10px 0 20px;display:flex;align-items:center;justify-content:space-between}
.f-input b{width:20px;height:20px;border-radius:50%;background:#111;display:flex;align-items:center;justify-content:center}
.social{top:3652px;width:46px;height:46px;border-radius:50%;border:1.5px solid var(--white);color:var(--white);font-size:12px;font-weight:700;display:flex;align-items:center;justify-content:center}
.f-divider{left:112px;top:3737px;width:976px;height:1px;background:rgba(255,255,255,.6)}
.f-bottom{top:3776px;font-size:13.5px;color:var(--white)}
.pay{top:3774px;width:32px;height:20px;border-radius:3px;background:#eef3fa}
</style>
</head>
<body>

<!-- Header -->
<header>
  <div class="abs topbar"></div>
  <div class="abs brand"><div class="brand-mark"></div><div class="brand-name">Firmora88</div></div>

  <div class="abs contact-item" style="left:270px">
    <span class="icon-dot"><svg width="16" height="12" viewBox="0 0 16 12"><rect x="1" y="1" width="14" height="10" rx="1.5" fill="none" stroke="#fff" stroke-width="1.6"/><path d="M1.5 1.8 8 7l6.5-5.2" fill="none" stroke="#fff" stroke-width="1.6"/></svg></span>
    support@firmora88.com.au
  </div>
  <div class="abs contact-item" style="left:581px">
    <span class="icon-dot"><svg width="16" height="16" viewBox="0 0 24 24"><path d="M6.6 10.8a15 15 0 0 0 6.6 6.6l2.2-2.2a1 1 0 0 1 1-.25 11.4 11.4 0 0 0 3.6.57 1 1 0 0 1 1 1V20a1 1 0 0 1-1 1A17 17 0 0 1 3 4a1 1 0 0 1 1-1h3.5a1 1 0 0 1 1 1c0 1.25.2 2.45.57 3.57a1 1 0 0 1-.25 1z" fill="#fff"/></svg></span>
    03 9000 4127
  </div>
  <div class="abs contact-item" style="left:763px">
    <span class="icon-dot"><svg width="18" height="18" viewBox="0 0 24 24"><circle cx="12" cy="12" r="8" fill="none" stroke="#fff" stroke-width="1.8"/><path d="M12 7v5l3 2" fill="none" stroke="#fff" stroke-width="1.8"/></svg></span>
    Customer Service
  </div>
  <div class="abs login">Login</div>

  <nav>
    <div class="abs navbar"></div>
    <span class="abs nav-link" style="left:83px">Register Company</span>
    <span class="abs nav-link" style="left:232px">Business Name</span>
    <span class="abs nav-link" style="left:359px">Set Up Trust</span>
    <span class="abs nav-link" style="left:466px">Set Up Business&nbsp; Plan</span>
    <span class="abs nav-link" style="left:636px">Register Trade Mark</span>
    <span class="abs nav-link" style="left:799px">More</span>
    <div class="abs search">Search<svg width="11" height="11" viewBox="0 0 12 12"><circle cx="5" cy="5" r="3.6" fill="none" stroke="#fff" stroke-width="1.6"/><path d="M8 8l3 3" stroke="#fff" stroke-width="1.6"/></svg></div>
  </nav>
</header>

<!-- Hero -->
<section>
  <div class="abs hero"></div>
  <div class="abs hero-photo" role="img" aria-label="Photo of two smiling colleagues working together at a laptop in a bright office"></div>
  <div class="abs hero-kicker">Welcome To</div>
  <div class="abs hero-title"><span class="sq"></span>Firmora88</div>
  <p class="abs hero-text">Lorem ipsum dolor sit amet, consectetur adipiscing elit, sed do eiusmod tempor incididunt ut labore et dolore magna aliqua.</p>
  <div class="abs btn hero-btn">Get Started</div>
  <div class="abs dots" style="left:566px;top:633px"><span class="on"></span><span></span><span></span><span></span></div>
</section>

<!-- About -->
<section>
  <div class="abs about-frame"></div>
  <div class="abs about-photo" role="img" aria-label="Photo of two business people reviewing documents together at a desk"></div>
  <h2 class="abs about-title">Welcome to Firmora88</h2>
  <p class="abs about-sub">Advanced, automated and simple company registration 24 hours a day.</p>
  <p class="abs about-text">We offer a fully automated, quick and cost effective company registration process. By completing an easy form, within 5 minutes you will receive full company registration documents setting up an Australian private company. We offer full customer support (telephone and email) 24 hours a day. It could not be any simpler, register your company today.</p>
  <div class="abs btn about-btn">Read More</div>
</section>

<!-- Reviews band -->
<section>
  <div class="abs band"></div>
  <p class="abs band-note">We take cybercrime and credit card fraud seriously. When you purchase a service through our site, we may collect your IP address for credit card security purposes</p>
  <div class="abs stars" style="left:436px;top:1257px">
    <svg width="22" height="21" viewBox="0 0 24 23"><path d="M12 0l3.1 7.6 8.2.6-6.3 5.3 2 8L12 17.2 5 21.5l2-8L.7 8.2l8.2-.6z" fill="var(--star)"/></svg>
    <svg width="22" height="21" viewBox="0 0 24 23"><path d="M12 0l3.1 7.6 8.2.6-6.3 5.3 2 8L12 17.2 5 21.5l2-8L.7 8.2l8.2-.6z" fill="var(--star)"/></svg>
    <svg width="22" height="21" viewBox="0 0 24 23"><path d="M12 0l3.1 7.6 8.2.6-6.3 5.3 2 8L12 17.2 5 21.5l2-8L.7 8.2l8.2-.6z" fill="var(--star)"/></svg>
    <svg width="22" height="21" viewBox="0 0 24 23"><path d="M12 0l3.1 7.6 8.2.6-6.3 5.3 2 8L12 17.2 5 21.5l2-8L.7 8.2l8.2-.6z" fill="var(--star)"/></svg>
    <svg width="22" height="21" viewBox="0 0 24 23"><path d="M12 0l3.1 7.6 8.2.6-6.3 5.3 2 8L12 17.2 5 21.5l2-8L.7 8.2l8.2-.6z" fill="var(--star)"/></svg>
  </div>
  <div class="abs leave">Leave Revora Review</div>

  <div class="abs avatar" style="left:101px;top:1329px"><span>M</span></div>
  <div class="abs rev-name" style="left:268px;top:1332px">Marcus Delany</div>
  <div class="abs stars" style="left:268px;top:1366px">
    <svg width="22" height="21" viewBox="0 0 24 23"><path d="M12 0l3.1 7.6 8.2.6-6.3 5.3 2 8L12 17.2 5 21.5l2-8L.7 8.2l8.2-.6z" fill="var(--star)"/></svg>
    <svg width="22" height="21" viewBox="0 0 24 23"><path d="M12 0l3.1 7.6 8.2.6-6.3 5.3 2 8L12 17.2 5 21.5l2-8L.7 8.2l8.2-.6z" fill="var(--star)"/></svg>
    <svg width="22" height="21" viewBox="0 0 24 23"><path d="M12 0l3.1 7.6 8.2.6-6.3 5.3 2 8L12 17.2 5 21.5l2-8L.7 8.2l8.2-.6z" fill="var(--star)"/></svg>
    <svg width="22" height="21" viewBox="0 0 24 23"><path d="M12 0l3.1 7.6 8.2.6-6.3 5.3 2 8L12 17.2 5 21.5l2-8L.7 8.2l8.2-.6z" fill="var(--star)"/></svg>
    <svg width="22" height="21" viewBox="0 0 24 23"><path d="M12 0l3.1 7.6 8.2.6-6.3 5.3 2 8L12 17.2 5 21.5l2-8L.7 8.2l8.2-.6z" fill="var(--star)"/></svg>
  </div>
  <p class="abs rev-text" style="left:268px;top:1398px;width:320px">Irena was extremely helpful and diligent. It was also very cheap. Great company and even better people!</p>

  <div class="abs avatar" style="left:625px;top:1329px"><span>T</span></div>
  <div class="abs rev-name" style="left:793px;top:1332px">tara wynn</div>
  <div class="abs stars" style="left:793px;top:1366px">
    <svg width="22" height="21" viewBox="0 0 24 23"><path d="M12 0l3.1 7.6 8.2.6-6.3 5.3 2 8L12 17.2 5 21.5l2-8L.7 8.2l8.2-.6z" fill="var(--star)"/></svg>
    <svg width="22" height="21" viewBox="0 0 24 23"><path d="M12 0l3.1 7.6 8.2.6-6.3 5.3 2 8L12 17.2 5 21.5l2-8L.7 8.2l8.2-.6z" fill="var(--star)"/></svg>
    <svg width="22" height="21" viewBox="0 0 24 23"><path d="M12 0l3.1 7.6 8.2.6-6.3 5.3 2 8L12 17.2 5 21.5l2-8L.7 8.2l8.2-.6z" fill="var(--star)"/></svg>
    <svg width="22" height="21" viewBox="0 0 24 23"><path d="M12 0l3.1 7.6 8.2.6-6.3 5.3 2 8L12 17.2 5 21.5l2-8L.7 8.2l8.2-.6z" fill="var(--star)"/></svg>
    <svg width="22" height="21" viewBox="0 0 24 23"><path d="M12 0l3.1 7.6 8.2.6-6.3 5.3 2 8L12 17.2 5 21.5l2-8L.7 8.2l8.2-.6z" fill="var(--star)"/></svg>
  </div>
  <p class="abs rev-text" style="left:793px;top:1398px;width:335px">Oskar and Irena were simply fantastic. I needed to set up a trust urgently and they were there to help every step of the way. Thank you so much for your outstanding service and I will most certainly be back!</p>
</section>

<!-- Video -->
<section>
  <div class="abs video"></div>
  <div class="abs video-art" role="img" aria-label="Line illustration of a woman working at a laptop on an office desk"></div>
  <div class="abs video-split"></div>
  <p class="abs video-text">Set up your company with us today at Firmora88</p>
  <div class="abs play"><svg width="49" height="49" viewBox="0 0 49 49"><path d="M19 14l15 10.5L19 35z" fill="#fff"/></svg></div>
</section>

<!-- How it works -->
<section>
  <div class="abs how"></div>
  <h2 class="abs section-title" style="top:2236px">HOW ITS WORK</h2>

  <div class="abs step" style="left:177px">
    <svg width="92" height="92" viewBox="0 0 92 92" fill="none" stroke="var(--blue-deep)" stroke-width="3">
      <rect x="8" y="6" width="56" height="78" rx="2"/>
      <path d="M18 22h36M18 32h36M18 42h30M18 52h24M18 62h20M18 72h14"/>
      <path d="M80 24l8 6-30 44-10 4 2-11z"/>
    </svg>
    <p>Fill in a short form</p>
  </div>

  <div class="abs step" style="left:477px">
    <svg width="92" height="92" viewBox="0 0 92 92" fill="none" stroke="var(--blue-deep)" stroke-width="3">
      <rect x="16" y="4" width="60" height="84" rx="2"/>
      <circle cx="46" cy="30" r="12"/>
      <path d="M40 30l4 4 8-8"/>
      <path d="M26 54h40M26 63h40M26 72h40M30 80h32"/>
    </svg>
    <p>Company registered in<br>less than 5 minutes</p>
  </div>

  <div class="abs step" style="left:779px">
    <svg width="96" height="92" viewBox="0 0 96 92" fill="none" stroke="var(--blue-deep)" stroke-width="3">
      <path d="M10 14h62M62 6l10 8-10 8"/>
      <path d="M86 32H24M34 24l-10 8 10 8"/>
      <path d="M6 50h14l10 26H12zM90 50H76L66 76h18z"/>
      <path d="M30 56l16-6 10 6 10-2M32 72l12 8 8-4 10 2 6-6"/>
    </svg>
    <p>Start trading using<br>your company</p>
  </div>
</section>

<!-- Testimonials -->
<section>
  <h2 class="abs section-title" style="top:2643px">TESTIMONIALS</h2>
  <div class="abs testi"></div>
  <div class="abs testi-photo" role="img" aria-label="Portrait photo of a smiling customer"></div>
  <div class="abs stars" style="left:678px;top:2766px">
    <svg width="22" height="21" viewBox="0 0 24 23"><path d="M12 0l3.1 7.6 8.2.6-6.3 5.3 2 8L12 17.2 5 21.5l2-8L.7 8.2l8.2-.6z" fill="var(--star)"/></svg>
    <svg width="22" height="21" viewBox="0 0 24 23"><path d="M12 0l3.1 7.6 8.2.6-6.3 5.3 2 8L12 17.2 5 21.5l2-8L.7 8.2l8.2-.6z" fill="var(--star)"/></svg>
    <svg width="22" height="21" viewBox="0 0 24 23"><path d="M12 0l3.1 7.6 8.2.6-6.3 5.3 2 8L12 17.2 5 21.5l2-8L.7 8.2l8.2-.6z" fill="var(--star)"/></svg>
    <svg width="22" height="21" viewBox="0 0 24 23"><path d="M12 0l3.1 7.6 8.2.6-6.3 5.3 2 8L12 17.2 5 21.5l2-8L.7 8.2l8.2-.6z" fill="var(--star)"/></svg>
    <svg width="22" height="21" viewBox="0 0 24 23"><path d="M12 0l3.1 7.6 8.2.6-6.3 5.3 2 8L12 17.2 5 21.5l2-8L.7 8.2l8.2-.6z" fill="var(--star)"/></svg>
  </div>
  <div class="abs testi-date">March&nbsp; 8th&nbsp;&nbsp; 2022</div>
  <p class="abs testi-quote">“I was surprised how easy and quick the process was. Great service at a fantastic price. Thank you”</p>
  <div class="abs testi-name">Daniel Hartwell</div>
  <div class="abs dots" style="left:568px;top:3092px"><span style="border-color:#999"></span><span class="on"></span><span style="border-color:#999"></span><span style="border-color:#999"></span></div>
</section>

<!-- Sponsors -->
<section>
  <h2 class="abs section-title" style="top:3173px;color:var(--blue-deep)">LIST OF SPONSORS</h2>
  <div class="abs arrow" style="left:127px"><svg width="10" height="14" viewBox="0 0 10 14"><path d="M8 1L2 7l6 6" fill="none" stroke="#333" stroke-width="2"/></svg></div>
  <div class="abs sponsor" style="left:146px;font-size:17px">Sitewave Traffic</div>
  <div class="abs sponsor" style="left:378px"><i></i>Tessera</div>
  <div class="abs sponsor" style="left:609px">Halden Finance</div>
  <div class="abs sponsor" style="left:842px">Roomlet</div>
  <div class="abs arrow" style="left:1037px"><svg width="10" height="14" viewBox="0 0 10 14"><path d="M2 1l6 6-6 6" fill="none" stroke="#333" stroke-width="2"/></svg></div>
</section>

<!-- Footer -->
<footer>
  <div class="abs footer"></div>

  <h3 class="abs f-head" style="left:112px">Quick links</h3>
  <div class="abs f-rule" style="left:112px"></div>
  <ul class="abs f-list" style="left:112px;list-style:none">
    <li>Register Company</li><li>Business Name</li><li>Set Up Trust</li><li>Set Up Business&nbsp; Plan</li><li>Register Trade Mark</li><li>More</li>
  </ul>

  <h3 class="abs f-head" style="left:304px">Latest News</h3>
  <div class="abs f-rule" style="left:304px"></div>
  <ul class="abs f-list" style="left:304px;list-style:none;line-height:30px;font-size:14px">
    <li>Terms&amp;condtions</li><li>Privacy Policy</li><li>About Us</li><li>Support</li>
  </ul>

  <h3 class="abs f-head" style="left:518px">Contact Us</h3>
  <div class="abs f-rule" style="left:518px"></div>
  <div class="abs" style="left:518px;top:3514px">
    <div class="f-label">ADDRESS</div>
    <div class="f-small"><svg width="9" height="12" viewBox="0 0 10 14"><path d="M5 0a5 5 0 0 1 5 5c0 4-5 9-5 9S0 9 0 5a5 5 0 0 1 5-5z" fill="#fff"/><circle cx="5" cy="5" r="1.8" fill="var(--footer)"/></svg> 14 Calder Lane KEWDALE<br>VIC 3150</div>
    <div class="f-label" style="margin-top:14px">PHONE</div>
    <div class="f-small"><svg width="11" height="11" viewBox="0 0 24 24"><path d="M6.6 10.8a15 15 0 0 0 6.6 6.6l2.2-2.2a1 1 0 0 1 1-.25 11.4 11.4 0 0 0 3.6.57 1 1 0 0 1 1 1V20a1 1 0 0 1-1 1A17 17 0 0 1 3 4a1 1 0 0 1 1-1h3.5a1 1 0 0 1 1 1c0 1.25.2 2.45.57 3.57a1 1 0 0 1-.25 1z" fill="#fff"/></svg> +61 3 90004127</div>
    <div class="f-label" style="margin-top:14px">EMAIL</div>
    <div class="f-small"><svg width="12" height="9" viewBox="0 0 16 12"><rect x="0" y="0" width="16" height="12" rx="1.5" fill="#fff"/><path d="M1 1l7 5 7-5" fill="none" stroke="var(--footer)" stroke-width="1.4"/></svg> support@firmora88.com.au</div>
  </div>

  <h3 class="abs f-head" style="left:813px">Newsletter</h3>
  <div class="abs f-rule" style="left:813px"></div>
  <p class="abs f-small" style="left:813px;top:3512px;width:290px">Lorem ipsum dolor sit amet, consectetur adipiscing elit, sed do eiusmod tempor</p>
  <div class="abs f-input">Enter Email<b><svg width="10" height="10" viewBox="0 0 10 10"><path d="M1 5l8-4-3 8-1-3z" fill="#fff"/></svg></b></div>
  <div class="abs social" style="left:817px">Nexo</div>
  <div class="abs social" style="left:874px">Vela</div>
  <div class="abs social" style="left:932px">Pix</div>

  <div class="abs f-divider"></div>
  <div class="abs f-bottom" style="left:112px">© Firmora88 Pty Ltd 2022. All Rights Reserved</div>
  <div class="abs pay" style="left:499px"></div>
  <div class="abs pay" style="left:538px"></div>
  <div class="abs pay" style="left:577px"></div>
  <div class="abs pay" style="left:616px"></div>
  <div class="abs pay" style="left:655px"></div>
  <div class="abs pay" style="left:694px"></div>
  <div class="abs pay" style="left:733px"></div>
  <div class="abs f-bottom" style="left:916px">Terms of use | Privacy Policy</div>
</footer>

</body>
</html>
```